Building Design company needing a letterhead

We need a letter head for our Building Design company to send letters etc. to our clients, consultants, councils etc. We would like to see our logo used and company colours. I have attached our style guide and an example of our current letterheads. Top left we would like our logo, top right we would like the company details and at the footer we would like some sort of image/design etc. that suits our brand. I like the Tarrow Design letterhead attached.

Target Market(s)

Professionals, Councils, Consultants, Mums & Dads

Industry/Entity Type

Architecture

Other font styles liked:
• refer the design style guide

Colors
f37122
000000
1b1b1b

Requirements
Must have
• Must have the minimum of a logo, company details and footer
Nice to have
• An image/design made for the footer that would suite our brand and website at www.corvanplans.com.au. Also it would be nice to include the KMEOT logo somewhere perhaps included in the footer.
Should not have
• Large images in the header. I just want the logo and company details.

```html
<!DOCTYPE html>
<html lang="en">
<head>
<meta charset="utf-8">
<title>Corvan Plans Letterhead</title>
<link rel="stylesheet" href="https://fonts.googleapis.com/css2?family=Arimo:wght@400&family=Ubuntu:wght@400;700&display=swap">
<style>
  :root {
    --paper: #f7f7f7;
    --ink: #1b1b1b;
    --black: #000000;
    --orange: #f37122;
    --band-dark: #3a3838;
  }
  html, body { margin: 0; padding: 0; overflow: hidden; }
  body { width: 1189px; height: 1200px; background: var(--paper); }
  .letterhead {
    position: relative; width: 1189px; height: 1200px; overflow: hidden;
    background: var(--paper); color: var(--ink);
  }
  .brand {
    position: absolute; left: 94px; top: 78px;
    display: flex; align-items: center; gap: 18px;
  }
  .brand-square { width: 58px; height: 58px; background: var(--orange); }
  .brand-name {
    font-family: "Ubuntu", sans-serif; font-weight: 700; font-size: 46px;
    letter-spacing: 2px; color: var(--ink); line-height: 1;
  }
  .company-details {
    position: absolute; left: 683px; top: 72px; margin: 0; padding: 0;
    list-style: none; font-family: "Ubuntu", sans-serif; font-size: 17.5px;
    line-height: 20.5px; color: var(--ink);
    transform: scaleX(1.18); transform-origin: left top;
  }
  .company-details li { display: flex; align-items: center; gap: 6px; white-space: nowrap; }
  .company-details svg { width: 14px; height: 14px; flex: none; }
  .abn-label { color: var(--orange); margin-left: 20px; margin-right: 5px; }
  .letter-body {
    position: absolute; left: 94px; top: 240px; width: 765px;
    font-family: "Arimo", sans-serif; font-size: 19.5px; line-height: 27.4px;
    color: var(--black); hyphens: auto;
    transform: scaleX(1.3); transform-origin: left top;
  }
  .letter-body p { margin: 0 0 27px; }
  .letter-body p.spaced { margin-top: 54px; }
  .member-mark {
    position: absolute; left: 94px; top: 1040px;
    display: flex; flex-direction: column; align-items: flex-start; gap: 8px;
  }
  .member-square { width: 66px; height: 66px; border: 3px solid var(--orange); box-sizing: border-box; }
  .member-name {
    font-family: "Ubuntu", sans-serif; font-weight: 400; font-size: 19px;
    letter-spacing: 1px; color: var(--orange);
  }
  .footer-graphic {
    position: absolute; left: 846px; top: 976px; width: 343px; height: 224px;
    background: linear-gradient(135deg, var(--band-dark) 0%, var(--band-dark) 45%, var(--orange) 100%);
  }
</style>
</head>
<body>
<div class="letterhead">
  <header>
    <div class="brand">
      <span class="brand-square"></span>
      <span class="brand-name">CORVAN PLANS</span>
    </div>
    <ul class="company-details">
      <li><svg viewBox="0 0 14 14"><rect width="14" height="14" fill="var(--orange)"/><path d="M2 4h10v7H2z M2 4l5 4 5-4" fill="none" stroke="#fff" stroke-width="1.2"/></svg>admin@corvanplans.com.au</li>
      <li><svg viewBox="0 0 14 14"><rect width="14" height="14" fill="var(--orange)"/><circle cx="7" cy="7" r="4.5" fill="none" stroke="#fff" stroke-width="1.1"/><path d="M2.5 7h9M7 2.5v9" stroke="#fff" stroke-width="1"/></svg>www.corvanplans.com.au</li>
      <li><svg viewBox="0 0 14 14"><rect width="14" height="14" fill="var(--orange)"/><path d="M7 12L3.8 7A3.4 3.4 0 1 1 10.2 7z" fill="#fff"/><circle cx="7" cy="5.4" r="1.3" fill="var(--orange)"/></svg>Unit 4/22 Ashby Road Fernleigh WA 6180</li>
      <li><svg viewBox="0 0 14 14"><rect width="14" height="14" fill="var(--orange)"/><path d="M7 12L3.8 7A3.4 3.4 0 1 1 10.2 7z" fill="#fff"/><circle cx="7" cy="5.4" r="1.3" fill="var(--orange)"/></svg>PO Box 3187 Fernleigh North WA 6180</li>
      <li><svg viewBox="0 0 14 14"><rect width="14" height="14" fill="var(--orange)"/><path d="M3 5.5c0-1.5 1-2 4-2s4 .5 4 2v1H9V5.5H5v1H3z M4 7h6l1 4H3z" fill="#fff"/></svg>(08) 6123 4870<span class="abn-label">ABN</span>40 718 293 516</li>
    </ul>
  </header>

  <main class="letter-body">
    <p>Lorem Ipsum is simply dummy text of the printing and typesetting industry. Lorem Ipsum has been the industry’s standard dummy text ever since the 1500s, when an unknown printer took a galley of type and scrambled it to make a type specimen book. It has survived not only five centuries, but also the leap into electronic typesetting, remaining essentially unchanged. It was popularised in the 1960s with the release of Lettrafax sheets containing Lorem Ipsum passages, and more recently with desktop publishing software like Pagewright Studio including versions of Lorem Ipsum.</p>
    <p>It is a long established fact that a reader will be distracted by the readable content of a page when looking at its layout. The point of using Lorem Ipsum is that it has a more-or-less normal distribution of letters, as opposed to using ’Content here, content here’, making it look like readable English. Many desktop publishing packages and web page editors now use Lorem Ipsum as their default model text, and a search for ’lorem ipsum’ will uncover many web sites still in their infancy. Various versions have evolved over the years, sometimes by accident, sometimes on purpose (injected humour and the like).</p>
    <p class="spaced">Contrary to popular belief, Lorem Ipsum is not simply random text. It has roots in a piece of classical Latin literature from 45 BC, making it over 2000 years old. Edwin Harrow, a Latin professor at Ashcombe College in Vermont, looked up one of the more obscure Latin words, consectetur, from a Lorem Ipsum passage, and going through the cites of the word in classical literature, discovered the undoubtable source. Lorem Ipsum comes from sections 1.10.32 and 1.10.33 of "de Finibus Bonorum et Malorum" structures, to generate Lorem Ipsum which looks reasonable. The generated Lorem Ipsum is therefore always free from repetition, injected humour, or non-characteristic words etc.</p>
  </main>

  <footer>
    <div class="member-mark">
      <span class="member-square"></span>
      <span class="member-name">KMEOT</span>
    </div>
    <div class="footer-graphic" role="img" aria-label="Footer graphic of angled dark grey and orange building blocks"></div>
  </footer>
</div>
</body>
</html>
```